Business Card Design for a Software Startup

We'd like to have a business card design. We already have a logo. Basically what we need is a clean design with name, address, cellphone and phone numbers, e-mail and web site address (front) and a space on the back with our logo with the company name on the right side and some texts on the bottom.
We are a development and consulting company in Brazil with highly qualified team of professionals in Java, iOS and Android development and consulting.

Target Market(s)

CIO, IT managers of mid to big size companies

Industry/Entity Type

Business

```html
<!DOCTYPE html>
<html lang="en">
<head>
<meta charset="utf-8">
<title>Velarq Business Card</title>
<link rel="stylesheet" href="https://fonts.googleapis.com/css2?family=Jost:wght@400;500;600;700&display=swap">
<style>
  :root {
    --backdrop: #e6e7ec;
    --card: #ffffff;
    --navy: #0a3f6e;
    --navy-deep: #082f55;
    --sky: #1ca8e6;
    --brand-blue: #0b4f87;
    --ink: #3a3d42;
    --label: #1b6fa8;
  }
  * { box-sizing: border-box; margin: 0; padding: 0; }
  html, body {
    width: 1200px; height: 987px; overflow: hidden;
    background: var(--backdrop);
    font-family: "Jost", "Futura", sans-serif;
  }
  .canvas { position: relative; width: 1200px; height: 987px; }

  .card {
    position: absolute;
    width: 620px; height: 355px;
    background: var(--card);
    border-radius: 34px;
    overflow: hidden;
    box-shadow: 0 6px 18px rgba(0,0,0,0.12);
  }
  .card--back  { left: 545px; top: 90px; }
  .card--front { left: 35px;  top: 520px; }

  /* back */
  .back-brand {
    position: absolute; left: 0; right: 0; top: 110px;
    display: flex; justify-content: center; align-items: center; gap: 22px;
  }
  .brand-square { width: 70px; height: 70px; background: var(--brand-blue); border-radius: 12px; }
  .brand-name {
    font-weight: 600; font-size: 60px; letter-spacing: 2px; color: var(--brand-blue);
  }
  .back-web {
    position: absolute; left: 0; right: 0; top: 228px; text-align: center;
    font-size: 21px; font-weight: 500; letter-spacing: 9px; color: var(--ink);
  }

  /* front */
  .name-marker { position: absolute; left: 16px; top: 22px; width: 13px; height: 44px; background: var(--navy); }
  .person { position: absolute; left: 44px; top: 18px; }
  .person-name { font-size: 29px; font-weight: 600; color: var(--brand-blue); line-height: 1.1; }
  .person-title { font-size: 19px; color: var(--ink); line-height: 1.1; }
  .address {
    position: absolute; left: 36px; top: 100px;
    font-size: 19px; line-height: 1.25; color: var(--ink);
  }
  .contacts {
    position: absolute; left: 36px; top: 168px;
    list-style: none; font-size: 19px; line-height: 1.25; color: var(--ink);
  }
  .contacts .label { color: var(--label); display: inline-block; width: 22px; }
  .front-brand {
    position: absolute; right: 40px; top: 150px;
    display: flex; align-items: center; gap: 16px;
  }
  .front-brand .brand-square { width: 52px; height: 52px; border-radius: 9px; }
  .front-brand .brand-name { font-size: 48px; }
  .bands { position: absolute; left: 0; bottom: 0; width: 620px; height: 120px; }
  .band-web {
    position: absolute; left: 30px; top: 272px;
    font-size: 15px; letter-spacing: 6px; color: #ffffff;
  }
</style>
</head>
<body>
<main class="canvas">

  <section class="card card--back" aria-label="Card back">
    <div class="back-brand">
      <span class="brand-square"></span>
      <span class="brand-name">VELARQ</span>
    </div>
    <p class="back-web">www.velarq.com</p>
  </section>

  <section class="card card--front" aria-label="Card front">
    <span class="name-marker"></span>
    <div class="person">
      <h1 class="person-name">Your Name</h1>
      <p class="person-title">Title</p>
    </div>
    <address class="address" style="font-style:normal">
      Door No. Street Name<br>
      City Name, State, Zip Code
    </address>
    <ul class="contacts">
      <li><span class="label">P:</span> 123-456-7890</li>
      <li><span class="label">C:</span> 123-456-7890</li>
      <li><span class="label">E:</span> yourname@velarq.com</li>
    </ul>
    <div class="front-brand">
      <span class="brand-square"></span>
      <span class="brand-name">VELARQ</span>
    </div>
    <svg class="bands" viewBox="0 235 620 120" preserveAspectRatio="none">
      <path d="M0 250 H300 C330 250 335 268 365 268 H620 V355 H0 Z" fill="var(--sky)"/>
      <path d="M0 268 H292 C325 268 332 290 368 290 H620 V355 H0 Z" fill="var(--navy)"/>
      <path d="M0 330 H620 V355 H0 Z" fill="var(--navy-deep)"/>
    </svg>
    <p class="band-web">www.velarq.com</p>
  </section>

</main>
</body>
</html>
```